Business Card Design

New business card design

Target Market(s)

Residential & Commercial Property Managers

Industry/Entity Type

Plumbing Services

Contact Information for Business Card

Name - Rowan Keddle, title - Director, Phone Number - 0431 286 517, email - rowan@tbk-plumbing.com.au, Company ABN - 73 215 904 386,

Font styles to use
Sans Serif

Colors
0054AA
0677BA
7BADD7
CADEEF
E8F1F8

```html
<!DOCTYPE html>
<html lang="en">
<head>
<meta charset="utf-8">
<title>TBK Plumbing Services – Business Card</title>
<link rel="stylesheet" href="https://fonts.googleapis.com/css2?family=Roboto:wght@400;500&display=swap">
<style>
  :root {
    --bg: #ececec;
    --cyan: #0aa5e8;
    --cyan-deep: #0677ba;
    --cyan-light: #4fc1f0;
    --ink: #1c1f24;
    --grey: #6a6a6a;
    --paper: #ffffff;
  }
  * { box-sizing: border-box; margin: 0; padding: 0; }
  html, body { width: 1200px; height: 900px; overflow: hidden; }
  body {
    background: var(--bg);
    font-family: "Roboto", Arial, sans-serif;
    position: relative;
  }
  .card {
    position: absolute;
    top: 301px;
    width: 520px;
    height: 297px;
    border-radius: 22px;
    overflow: hidden;
    box-shadow: 0 10px 28px rgba(0,0,0,0.18);
  }
  .card-front { left: 60px; background: var(--paper); border: 3px solid var(--cyan); }
  .card-back { left: 620px; }

  .name-band {
    position: absolute;
    top: 0; left: 0;
    width: 300px; height: 40px;
    background: var(--cyan);
    color: var(--paper);
    font-weight: 500;
    font-size: 19px;
    letter-spacing: 0.2px;
    line-height: 40px;
    padding-left: 24px;
    text-transform: uppercase;
  }
  .job-title {
    position: absolute;
    top: 46px; left: 24px;
    font-size: 13px;
    color: var(--grey);
  }
  .brand {
    position: absolute;
    top: 48px; left: 318px;
    width: 180px;
    display: flex; align-items: flex-start; gap: 10px;
    font-size: 28px; font-weight: 400;
    line-height: 32px;
    color: var(--ink);
  }
  .brand-dot { width: 14px; height: 14px; margin-top: 10px; border-radius: 50%; background: var(--cyan); flex: none; }
  .contact-list {
    position: absolute;
    top: 150px; left: 22px;
    list-style: none;
    font-size: 15px;
    color: var(--grey);
    line-height: 22px;
  }
  .contact-list li { display: flex; align-items: center; gap: 6px; }
  .contact-list svg { width: 13px; height: 13px; fill: var(--cyan-deep); }
  .abn {
    position: absolute;
    right: 26px; bottom: 22px;
    font-size: 19px;
    color: var(--grey);
  }
  .abn-label { color: var(--cyan); }

  .drop-pattern {
    position: absolute; inset: 0;
    background: linear-gradient(120deg, var(--cyan-deep) 0%, var(--cyan) 55%, var(--cyan-light) 100%);
  }
  .back-brand {
    position: absolute;
    top: 50%; left: 50%;
    transform: translate(-50%, -50%);
    display: flex; align-items: center; gap: 12px;
    font-size: 26px; font-weight: 400;
    color: var(--paper);
    white-space: nowrap;
  }
  .back-dot { width: 16px; height: 16px; border-radius: 50%; background: var(--paper); flex: none; }
</style>
</head>
<body>
  <section class="card card-front" aria-label="Business card front">
    <div class="name-band">Rowan Keddle</div>
    <div class="job-title">Director</div>
    <div class="brand"><span class="brand-dot"></span><span>TBK Plumbing Services</span></div>
    <ul class="contact-list">
      <li>
        <svg viewBox="0 0 24 24" aria-hidden="true"><path d="M6.6 10.8a15.1 15.1 0 0 0 6.6 6.6l2.2-2.2a1 1 0 0 1 1-.25 11.4 11.4 0 0 0 3.6.57 1 1 0 0 1 1 1V20a1 1 0 0 1-1 1A17 17 0 0 1 3 4a1 1 0 0 1 1-1h3.5a1 1 0 0 1 1 1c0 1.25.2 2.45.57 3.57a1 1 0 0 1-.25 1z"/></svg>
        0431 286 517
      </li>
      <li>
        <svg viewBox="0 0 24 24" aria-hidden="true"><path d="M2 5h20v14H2zm2 2v.5l8 5 8-5V7l-8 5z"/></svg>
        rowan@tbk-plumbing.com.au
      </li>
    </ul>
    <div class="abn"><span class="abn-label">ABN:</span> 73 215 904 386</div>
  </section>

  <section class="card card-back" aria-label="Business card back">
    <div class="drop-pattern" role="img" aria-label="Repeating pattern of blue water drops"></div>
    <div class="back-brand"><span class="back-dot"></span>TBK Plumbing Services</div>
  </section>
</body>
</html>
```